Agriculture Business Card

I want to use my existing logo and use my tagline of "Don't Guess...Soil Test" on the card. Looking for a double sided card that will really get peoples attention.
Contact Info:
Marlow Field Crop Edge
Calvin Brusk
2917 K Lane
Larkin, NE 68593
402-555-0193
calvin.r.brusk@fieldmailbox.net

```html
<!DOCTYPE html>
<html lang="en">
<head>
<meta charset="utf-8">
<title>Marlow Field Crop Edge — Business Card</title>
<link href="https://fonts.googleapis.com/css2?family=Montserrat:wght@400;700&display=swap" rel="stylesheet">
<style>
  :root{
    --backdrop:#d6d6d6;
    --paper:#ecebe8;
    --soil:#955539;
    --name-brown:#a4603f;
    --leaf:#3cb43a;
    --ink:#5e5e5e;
    --white:#ffffff;
  }
  *{box-sizing:border-box;margin:0;padding:0}
  html,body{width:1200px;height:1051px;overflow:hidden;background:var(--backdrop)}
  body{font-family:"Montserrat",sans-serif;position:relative}
  .card{
    position:absolute;left:220px;width:760px;height:434px;
    border-bottom:5px solid var(--leaf);
    box-shadow:0 14px 30px rgba(0,0,0,.18);
  }
  .card--front{top:62px;background:var(--paper)}
  .card--back{top:555px;background:var(--soil);display:flex;align-items:center;justify-content:center}

  .holder-name{
    position:absolute;left:110px;top:150px;
    font-weight:700;font-size:30px;letter-spacing:1px;color:var(--name-brown);text-transform:uppercase;
  }
  .divider{position:absolute;left:355px;top:130px;width:2px;height:110px;background:var(--leaf)}
  .contact{position:absolute;left:385px;top:130px;font-size:19px;line-height:27px;color:var(--ink);list-style:none}
  .contact li{display:flex;align-items:center;gap:8px}
  .contact .plain{padding-left:0}
  .contact svg{width:16px;height:16px;flex:none;fill:var(--leaf)}
  .tagline{
    position:absolute;left:0;right:0;top:335px;text-align:center;
    font-size:22px;letter-spacing:1px;color:var(--ink);
  }

  .brand{display:flex;align-items:center;gap:18px}
  .brand-dot{width:34px;height:34px;border-radius:50%;background:var(--white)}
  .brand-name{font-weight:700;font-size:38px;color:var(--white);line-height:1.15;text-align:left}
</style>
</head>
<body>
  <section class="card card--front">
    <h1 class="holder-name">Calvin Brusk</h1>
    <span class="divider"></span>
    <ul class="contact">
      <li class="plain">2917 K Lane</li>
      <li class="plain">Larkin, NE 68593</li>
      <li>
        <svg viewBox="0 0 24 24" aria-hidden="true"><path d="M6.6 10.8a15.1 15.1 0 0 0 6.6 6.6l2.2-2.2a1 1 0 0 1 1-.25 11.4 11.4 0 0 0 3.6.6 1 1 0 0 1 1 1V20a1 1 0 0 1-1 1A17 17 0 0 1 3 4a1 1 0 0 1 1-1h3.5a1 1 0 0 1 1 1c0 1.25.2 2.45.6 3.6a1 1 0 0 1-.25 1z"/></svg>
        402-555-0193
      </li>
      <li>
        <svg viewBox="0 0 24 24" aria-hidden="true"><path d="M2 5h20v14H2z M2 5l10 8 10-8" fill="var(--leaf)" stroke="var(--paper)" stroke-width="1.5"/></svg>
        calvin.r.brusk@fieldmailbox.net
      </li>
    </ul>
    <p class="tagline">Don't Guess...Soil Test</p>
  </section>

  <section class="card card--back">
    <div class="brand">
      <span class="brand-dot"></span>
      <span class="brand-name">Marlow Field<br>Crop Edge</span>
    </div>
  </section>
</body>
</html>
```